Upscale business cards needed for Board of Directors

We need professional business cards created for members of our family business Board of Directors. We would like these relatively simple and straightforward, but also with a unique element to set them apart. Probably stick with neutral and simple colors - white, grey etc. We need space for the traditional elements, including name, title, address, email/phone number. And we will be creating several from this template so it needs to be template that is easy to switch information in and out of.
Business
See description

```html
<!DOCTYPE html>
<html lang="en">
<head>
<meta charset="UTF-8">
<title>Harborline Holdings – Business Card</title>
<link rel="stylesheet" href="https://fonts.googleapis.com/css2?family=Cinzel:wght@400;600&family=Lato:wght@400;900&family=Courier+Prime&display=swap">
<style>
  :root {
    --backdrop: #e9e7e3;
    --card: #ffffff;
    --band: #8a8a8a;
    --ink: #1d1d1d;
    --light: #ffffff;
    --icon-ink: #8a8a8a;
  }
  * { box-sizing: border-box; margin: 0; padding: 0; }
  html, body { width: 1200px; height: 799px; overflow: hidden; background: var(--backdrop); }
  .card {
    position: absolute; left: 100px; top: 114px;
    width: 1000px; height: 571px;
    background: var(--card);
    overflow: hidden;
    box-shadow: 0 10px 30px rgba(0,0,0,0.18);
  }
  .brand {
    position: absolute; top: 70px; left: 0; width: 100%;
    text-align: center;
    font-family: "Lato", sans-serif; font-weight: 900;
    font-size: 58px; letter-spacing: 2px; line-height: 1;
    color: var(--ink); text-transform: uppercase;
  }
  .name-panel {
    position: absolute; left: 0; top: 215px;
    width: 470px; height: 205px;
    background: var(--band);
    border-radius: 0 44px 44px 0;
    padding: 42px 0 0 44px;
    color: var(--light);
  }
  .name-panel .name {
    font-family: "Cinzel", serif; font-weight: 600;
    font-size: 34px; letter-spacing: 1px;
  }
  .name-panel .title {
    font-family: "Courier Prime", monospace;
    font-size: 22px; letter-spacing: 2px; margin-top: 2px;
  }
  .contact-panel {
    position: absolute; left: 510px; top: 255px;
    width: 490px; height: 225px;
    background: var(--band);
    border-radius: 44px 0 0 44px;
    padding: 26px 0 0 44px;
    list-style: none;
    font-family: "Lato", sans-serif; font-size: 21px;
    color: var(--light); line-height: 1.2;
  }
  .contact-panel li { display: flex; align-items: flex-start; gap: 16px; margin-bottom: 12px; }
  .contact-panel svg { flex: none; width: 24px; height: 24px; margin-top: 1px; }
</style>
</head>
<body>
  <div class="card">
    <div class="brand">Harborline Holdings</div>

    <div class="name-panel">
      <div class="name">Name Surname</div>
      <div class="title">Designation</div>
    </div>

    <ul class="contact-panel">
      <li>
        <svg viewBox="0 0 24 24"><circle cx="12" cy="12" r="12" fill="#fff"/><path d="M12 5a4.5 4.5 0 0 0-4.5 4.5C7.5 13 12 19 12 19s4.5-6 4.5-9.5A4.5 4.5 0 0 0 12 5zm0 6.2a1.7 1.7 0 1 1 0-3.4 1.7 1.7 0 0 1 0 3.4z" fill="var(--icon-ink)"/></svg>
        <span>118 W. Cedar Grove Ave.<br>Millbrook, TX. 75021</span>
      </li>
      <li>
        <svg viewBox="0 0 24 24"><circle cx="12" cy="12" r="12" fill="#fff"/><path d="M8.6 6.5l1.8 2.3-1 1.4a8 8 0 0 0 4.4 4.4l1.4-1 2.3 1.8-.9 2a2 2 0 0 1-1.8.6A10 10 0 0 1 6.6 9.8a2 2 0 0 1 .6-1.8z" fill="var(--icon-ink)"/></svg>
        <span>(555) 210 - 4836</span>
      </li>
      <li>
        <svg viewBox="0 0 24 24"><circle cx="12" cy="12" r="12" fill="#fff"/><rect x="6" y="8" width="12" height="8.5" rx="1" fill="var(--icon-ink)"/><path d="M6.5 8.7L12 12.8l5.5-4.1" stroke="#fff" stroke-width="1.2" fill="none"/></svg>
        <span>Mark@NorthvaleCapital.co</span>
      </li>
      <li>
        <svg viewBox="0 0 24 24"><circle cx="12" cy="12" r="12" fill="#fff"/><g stroke="var(--icon-ink)" stroke-width="1.3" fill="none"><circle cx="12" cy="12" r="6"/><ellipse cx="12" cy="12" rx="2.6" ry="6"/><path d="M6 12h12"/></g></svg>
        <span>www.NorthvaleCapital.co</span>
      </li>
    </ul>
  </div>
</body>
</html>
```